Road Construction Company needs business cards

We would like a new business card designed for our business.

We're a road construction company based in Qld, Australia.

Can the business card please have the following information on it.

Name: Warren Halbeck
Position: General Manager
Phone: 0472 915 348
Email: Warren.halbeck@tovrin.com.au
Address: 87 Marrow Ave, Pendlebay, QLD, 4023
Website: www.tovrin.com.au

Visually we'd like the card to be professional and simple.

Attached is our logo.

Our website is www.tovrin.com.au

Target Market(s)

Men aged 25-60

Contact Information for Business Card

As listed in project description

Font styles to use
Serif

Requirements
Must have
• Large logo on back of card

```html
<!DOCTYPE html>
<html lang="en">
<head>
<meta charset="utf-8">
<title>Tovrin Business Card</title>
<link href="https://fonts.googleapis.com/css2?family=Michroma&display=swap" rel="stylesheet">
<style>
  :root {
    --backdrop: #616161;
    --brand-blue: #0b53a3;
    --ink-blue: #1553a0;
    --card-white: #ffffff;
  }
  * { margin: 0; padding: 0; box-sizing: border-box; }
  html, body {
    width: 1072px;
    height: 1200px;
    overflow: hidden;
    background: var(--backdrop);
    font-family: "Michroma", "Arial", sans-serif;
  }
  .sheet {
    position: relative;
    width: 1072px;
    height: 1200px;
  }
  .card {
    position: absolute;
    top: 452px;
    width: 520px;
    height: 296px;
  }
  .card--front { left: 10px; background: var(--brand-blue); }
  .card--back { left: 544px; background: var(--card-white); color: var(--ink-blue); }

  .wordmark {
    font-family: "Michroma", "Arial", sans-serif;
    letter-spacing: 0.02em;
    line-height: 1;
    white-space: nowrap;
  }
  .card--front .wordmark {
    position: absolute;
    left: 0; right: 0;
    top: 126px;
    text-align: center;
    font-size: 38px;
    color: var(--card-white);
  }
  .card--back .wordmark {
    position: absolute;
    right: 52px;
    top: 54px;
    font-size: 17px;
    color: var(--ink-blue);
  }

  .holder {
    position: absolute;
    left: 54px;
    top: 92px;
  }
  .holder__name {
    font-size: 9px;
    letter-spacing: 0.06em;
  }
  .holder__name strong {
    font-size: 12.5px;
    font-weight: 400;
    letter-spacing: 0.06em;
  }
  .holder__role {
    margin: 5px 0 0 13px;
    font-size: 7.5px;
    letter-spacing: 0.06em;
  }
  .divider {
    position: absolute;
    left: 54px;
    top: 139px;
    width: 174px;
    height: 1px;
    background: var(--ink-blue);
  }
  .contact {
    position: absolute;
    left: 54px;
    top: 158px;
    list-style: none;
    font-size: 8px;
    letter-spacing: 0.07em;
    line-height: 14.5px;
  }
</style>
</head>
<body>
  <main class="sheet">
    <section class="card card--front" aria-label="Card front">
      <div class="wordmark">TOVRIN</div>
    </section>

    <section class="card card--back" aria-label="Card back">
      <div class="wordmark">TOVRIN</div>
      <div class="holder">
        <p class="holder__name">Name: Warren <strong>Halbeck</strong></p>
        <p class="holder__role">Position: General Manager</p>
      </div>
      <div class="divider"></div>
      <ul class="contact">
        <li>Email: Warren.halbeck@tovrin.com.au</li>
        <li>Address: 87 Marrow Ave, Pendlebay, QLD, 4023</li>
        <li>Phone: 0472 915 348</li>
        <li>Website: www.tovrin.com.au</li>
      </ul>
    </section>
  </main>
</body>
</html>
```